Luxury Real Estate Website, Midwest, United States

We need web design services for a luxury website. We need IDX Integration with our MLS. We want this to be a very simple website with amazing graphics. We want it to link up with our MailChimp account in order to generate leads through a "More Information" Pop up on the main page. We want the main page to be covered with one large graphic that is a rolling slideshow of active listings of $400,000 and up from the IDX Integration. We need this website to give a very exclusive and sleek look. Lots of black is good... I will upload our logos in Black and Silver. We will also need an "About" page that we are going to call "Qeno Info". We want our graphics to be extremely impressive. Keep in mind, we are a company in the Midwest of the United States, and our real estate has a different look than homes in California or Florida. We need graphics that are realistic for the Midwest, yet still high-end.
Target Market(s)
Luxury Homeowners in the Midwest United States. The graphics needs to be pristine.
Industry/Entity Type
Real Estate
Coding
Coded - Design and coding required
Number of Pages Required
3 page
Requirements
Must have
- Large graphics with IDX Integration. The photos of real estate need to represent real estate that is common in the Midwest, United States. We also need MailChimp integration. We need a pop up that is titled "My Free Market Analysis" that makes them fill out a contact form asking for Full Name, Email Address, Phone Number and Address. This needs to be a pop up on the front page and will integrate with our MailChimp account. We also need a page called "About Qe No Home". And another page where clients can download informational PDFs. The main component needs to be a front page search engine connected with the IDX to access active listings from our MLS. I attached our logos and a sample front page of a website. I would love for ours to look similar.
Nice to have
- Lake House photos on midwest lakes are a plus.
Should not have
- Should not have clutter. This website needs to be clean, luxurious and exclusive.

```html
<!DOCTYPE html>
<html lang="en">
<head>
<meta charset="utf-8">
<title>Hearthline Realty Group</title>
<link href="https://fonts.googleapis.com/css2?family=Didact+Gothic&family=Montserrat:wght@600;700&display=swap" rel="stylesheet">
<style>
:root{
  --ink:#1b1b1b;
  --footer:#1c1c1c;
  --white:#ffffff;
  --text:#3a3a3a;
  --muted:#6b6b6b;
  --footer-text:#5e5e5e;
  --rule:#8a8a8a;
  --line:#2e2e2e;
}
*{box-sizing:border-box;margin:0;padding:0}
html,body{width:1200px;height:2514px;overflow:hidden}
body{position:relative;background:var(--white);font-family:"Didact Gothic",Arial,sans-serif;color:var(--text)}
.abs{position:absolute}
.center{left:0;width:1200px;text-align:center}

/* header */
.site-header{position:absolute;left:0;top:0;width:1200px;height:112px;background:var(--ink);z-index:3}
.brand{position:absolute;left:100px;top:44px;display:flex;align-items:center;gap:10px;color:var(--white);font-size:24px;letter-spacing:2px}
.brand-square{width:14px;height:14px;background:var(--white)}
.main-nav{position:absolute;top:56px;left:0;width:1200px;font-size:13px;color:var(--white);text-transform:uppercase;letter-spacing:.3px}
.main-nav a{position:absolute;color:inherit;text-decoration:none}
.main-nav .active::after{content:"";position:absolute;left:-2px;right:-2px;top:24px;height:3px;border-radius:2px;background:var(--rule)}

/* hero */
.hero{position:absolute;left:0;top:112px;width:1200px;height:614px;overflow:hidden}
.hero-photo{position:absolute;inset:0;background:
  linear-gradient(rgba(0,0,0,.28),rgba(0,0,0,.18)),
  linear-gradient(180deg,#7e7466 0%,#8d7f6c 35%,#5f6a3c 62%,#4f7a2c 80%,#3f6b22 100%)}
.hero-title{position:absolute;top:170px;left:0;width:1200px;text-align:center;font-family:"Montserrat",Arial,sans-serif;font-weight:700;font-size:62px;color:var(--white);letter-spacing:1px}
.hero-sub{position:absolute;top:252px;left:0;width:1200px;text-align:center;font-size:19px;color:var(--white)}
.hero-arrow{position:absolute;top:283px}
.hero-curve{position:absolute;left:0;bottom:0}

/* sections */
.section-title{position:absolute;left:0;width:1200px;text-align:center;font-size:36px;color:#222}
.title-rule{position:absolute;left:578px;width:44px;height:3px;border-radius:2px;background:var(--rule)}
.welcome-copy{position:absolute;left:120px;width:960px;text-align:center;font-size:14.5px;line-height:26px;color:var(--text)}
.btn-outline{position:absolute;left:527px;top:1040px;width:146px;height:45px;border:1.5px solid #333;font-size:17px;color:#222;display:flex;align-items:center;justify-content:center}

.properties-divider{position:absolute;left:0;top:1175px;width:1200px;height:1px;background:#f0f0f0}
.property-tile{position:absolute;width:230px;height:193px}
.property-overlay{position:absolute;inset:0;background:rgba(20,20,20,.72);color:var(--white);text-align:center}
.property-overlay .city{margin-top:54px;font-size:26px;letter-spacing:2px}
.property-overlay .meta{font-size:15px;line-height:26px;letter-spacing:1px}

.feature-band{position:absolute;left:0;top:1802px;width:1200px;height:347px;background:
  linear-gradient(rgba(30,38,52,.55),rgba(30,38,52,.55)),
  linear-gradient(180deg,#3d4d66 0%,#4a5468 45%,#6b6a66 75%,#56524c 100%)}
.feature-title{position:absolute;top:92px;left:0;width:1200px;text-align:center;font-size:35px;color:var(--white)}
.feature-copy{position:absolute;top:160px;left:160px;width:880px;text-align:center;font-size:16px;line-height:32px;color:var(--white)}

/* footer */
.site-footer{position:absolute;left:0;top:2149px;width:1200px;height:365px;background:var(--footer);color:var(--footer-text)}
.footer-brand{position:absolute;left:100px;top:98px;display:flex;align-items:center;gap:10px;color:var(--white);font-size:22px;letter-spacing:2px}
.footer-about{position:absolute;left:100px;top:162px;width:240px;font-size:10px;line-height:17px}
.footer-heading{position:absolute;top:52px;font-family:"Montserrat",Arial,sans-serif;font-weight:600;font-size:13px;color:var(--white)}
.footer-heading::after{content:"";position:absolute;left:0;top:24px;width:44px;height:3px;border-radius:2px;background:#555}
.link-list{position:absolute;top:107px;list-style:none;font-size:13px;line-height:28.5px}
.contact-list{position:absolute;left:858px;top:107px;list-style:none;font-size:13px;line-height:28.5px}
.contact-list li{display:flex;align-items:center;gap:10px}
.contact-list svg{flex:none}
.contact-list .indent{padding-left:22px}
.footer-rule{position:absolute;left:100px;top:296px;width:1000px;height:1px;background:var(--line)}
.copyright{position:absolute;top:318px;left:0;width:1200px;text-align:center;font-size:11px}
</style>
</head>
<body>

<header class="site-header">
  <div class="brand"><span class="brand-square"></span>HEARTHLINE</div>
  <nav class="main-nav">
    <a class="active" style="left:505px">Home</a>
    <a style="left:594px">Qeno Info</a>
    <a style="left:712px">About Qe No Home</a>
    <a style="left:887px">Downloads</a>
    <a style="left:1023px">Contact Us</a>
  </nav>
</header>

<section class="hero">
  <div class="hero-photo" role="img" aria-label="Large stone and brick Midwest luxury home with arched entry, landscaped lawn and curved walkway"></div>
  <h1 class="hero-title">HEARTHLINE REALTY GROUP</h1>
  <p class="hero-sub">We are a luxury real estate company from Midwest, United states</p>
  <svg class="hero-arrow" style="left:32px" width="16" height="30" viewBox="0 0 16 30"><path d="M14 2 2 15l12 13" fill="none" stroke="rgba(255,255,255,.6)" stroke-width="2"/></svg>
  <svg class="hero-arrow" style="left:1150px" width="16" height="30" viewBox="0 0 16 30"><path d="M2 2l12 13L2 28" fill="none" stroke="rgba(255,255,255,.6)" stroke-width="2"/></svg>
  <svg class="hero-curve" width="1200" height="70" viewBox="0 0 1200 70"><path d="M0 70Q600-45 1200 70Z" fill="#fff"/></svg>
</section>

<section class="welcome">
  <h2 class="section-title" style="top:748px">Welcome to Hearthline Realty Group</h2>
  <div class="title-rule" style="top:800px"></div>
  <p class="welcome-copy" style="top:822px">Lorem ipsum dolor sit amet, consectetur adipiscing elit, sed do eiusmod tempor incididunt ut labore et dolore magna aliqua. Ut enim ad minim veniam, quis nostrud exercitation ullamco laboris nisi ut aliquip ex ea commodo consequat. Duis aute irure dolor in reprehenderit in voluptate velit esse cillum dolore eu fugiat nulla pariatur.</p>
  <p class="welcome-copy" style="top:925px">Sed ut perspiciatis unde omnis iste natus error sit voluptatem accusantium doloremque laudantium, totam rem aperiam, eaque ipsa quae ab illo inventore veritatis et quasi architecto beatae vitae dicta sunt explicabo.</p>
  <div class="btn-outline">Learn more</div>
</section>

<section class="properties">
  <div class="properties-divider"></div>
  <h2 class="section-title" style="top:1212px">Our Properties</h2>
  <div class="title-rule" style="top:1262px"></div>

  <div class="property-tile" style="left:100px;top:1307px;background:linear-gradient(#5a5e62,#3e4a36)" role="img" aria-label="Two-storey family home at dusk">
    <div class="property-overlay">
      <p class="city">CALIFORNIA</p>
      <p class="meta">48 Linden Street<br>Price on request</p>
    </div>
  </div>
  <div class="property-tile" style="left:357px;top:1307px;background:linear-gradient(#9cc0e4 0%,#a66e58 45%,#5e8f3a 75%,#6aa23d)" role="img" aria-label="Red brick house with large lawn"></div>
  <div class="property-tile" style="left:613px;top:1307px;background:linear-gradient(#3f6b3a 0%,#5a5242 45%,#7a93aa 70%,#9bb2c8)" role="img" aria-label="Lake house among trees on the water"></div>
  <div class="property-tile" style="left:870px;top:1307px;background:linear-gradient(#e29a7a 0%,#b07a72 30%,#6c4a36 65%,#5a3a28)" role="img" aria-label="Timber homes on a hillside at sunset"></div>

  <div class="property-tile" style="left:100px;top:1522px;background:linear-gradient(#d2d6da 0%,#7a5a44 45%,#8a6a4e 70%,#5e8a3a)" role="img" aria-label="Craftsman bungalow with porch and garden"></div>
  <div class="property-tile" style="left:357px;top:1522px;background:linear-gradient(#7fb0dc 0%,#a27a62 40%,#8a7060 65%,#4f8a30)" role="img" aria-label="Brick suburban home with garage and green lawn"></div>
  <div class="property-tile" style="left:613px;top:1522px;background:linear-gradient(#4d6a38 0%,#8a4a46 40%,#d8d2c8 65%,#4e7e2e)" role="img" aria-label="Red painted house with white porch"></div>
  <div class="property-tile" style="left:870px;top:1522px;background:linear-gradient(#7ab2e0 0%,#a8c4d8 35%,#8a7a5e 55%,#3f7fa0 75%,#5a9a3a)" role="img" aria-label="Lakeside estate reflected in calm water"></div>
</section>

<section class="feature-band" role="img" aria-label="Grand estate with turrets at twilight">
  <h2 class="feature-title">Feature Projects</h2>
  <p class="feature-copy">At vero eos et accusamus et iusto odio dignissimos ducimus qui blanditiis praesentium voluptatum deleniti atque corrupti quos dolores et quas molestias excepturi sint occaecati cupiditate non provident</p>
</section>

<footer class="site-footer">
  <div class="footer-brand"><span class="brand-square"></span>HEARTHLINE</div>
  <p class="footer-about">Crafted for those who expect more from a home, we guide every step with care, discretion and a deep knowledge of the Midwest market.</p>

  <h3 class="footer-heading" style="left:449px">QUICK LINKS</h3>
  <ul class="link-list" style="left:449px">
    <li>Home</li><li>Qeno Info</li><li>About Qe No Home</li><li>Downloads</li><li>Contact us</li>
  </ul>
  <ul class="link-list" style="left:645px">
    <li>Terms &amp; Conditions</li><li>Privacy Policy</li><li>Contact</li>
  </ul>

  <h3 class="footer-heading" style="left:858px">CONTACT US</h3>
  <ul class="contact-list">
    <li><svg width="12" height="14" viewBox="0 0 12 14"><path d="M6 0a5 5 0 0 0-5 5c0 4 5 9 5 9s5-5 5-9a5 5 0 0 0-5-5zm0 7a2 2 0 1 1 0-4 2 2 0 0 1 0 4z" fill="#fff"/></svg>Hearthline Realty Group</li>
    <li class="indent">Street Address, City Name, Country.</li>
    <li><svg width="12" height="12" viewBox="0 0 12 12"><path d="M2.5 0 5 3 3.6 4.6a7 7 0 0 0 3.8 3.8L9 7l3 2.5-1.5 2C5 11.5.5 7 .5 1.5z" fill="#fff"/></svg>01234 98765</li>
    <li><svg width="12" height="10" viewBox="0 0 12 10"><path d="M0 0h12v10H0z" fill="#fff"/><path d="M0 0l6 5 6-5" fill="none" stroke="#1c1c1c" stroke-width="1.2"/></svg>hello@hearthlinerealty.com</li>
    <li><svg width="12" height="12" viewBox="0 0 12 12"><circle cx="6" cy="6" r="6" fill="#fff"/><path d="M0 6h12M6 0c-3 3-3 9 0 12M6 0c3 3 3 9 0 12" fill="none" stroke="#1c1c1c" stroke-width=".9"/></svg>www.hearthlinerealty.com</li>
  </ul>

  <div class="footer-rule"></div>
  <p class="copyright">© 2018 HEARTHLINE REALTY GROUP.  All right reserved . Term of Use</p>
</footer>

</body>
</html>
```